Luxury Business Card Design for High-End Window Treatments

Gilded Slatworks
Custom Plantation Shutters & Architectural Shading Systems

⸻

BACK

Daniel Trevick
Owner

Custom Interior & Exterior Window Treatments

919-555-0148
gildedslatworks.com

I have included a picture that I’m hoping we can use on the back, but I’m also wondering if you can get rid of the ladder? Should we get rid of shutters , shades and blinds underneath Gilded Slatworks?

Target Market(s)

High-end residential homeowners, custom home builders, architects, interior designers, and luxury renovation clients seeking premium plantation shutters and motorized architectural shading systems.

Industry/Entity Type

Custom Window treatments

Contact Information for Business Card

Front Gilded Slatworks Custom Plantation Shutters Motorized Architectural Shading Systems BACK Daniel Trevick Owner 919-555-0148 GildedSlatworks.com Custom Interior & Exterior Window Treatments By Appointment

Requirements
Nice to have
• Not 100% sure on nice to halves or the color but you can definitely check out my website to get a better understanding of what I’m trying to do

```html
<!DOCTYPE html>
<html lang="en">
<head>
<meta charset="utf-8">
<title>Gilded Slatworks — Business Card</title>
<link href="https://fonts.googleapis.com/css2?family=Lato:wght@400;700&family=Lora:wght@400;700&display=swap" rel="stylesheet">
<style>
  :root {
    --backdrop: #1e1d1d;
    --card-black: #0b0b0b;
    --ivory: #ece6d6;
    --gold: #f0b93a;
    --text-light: #e9e9e9;
    --photo-top: #1b2130;
    --photo-bottom: #121416;
  }
  * { margin: 0; padding: 0; box-sizing: border-box; }
  html, body { width: 1200px; height: 939px; overflow: hidden; background: var(--backdrop); }
  .canvas { position: relative; width: 1200px; height: 939px; }

  .card {
    position: absolute;
    width: 520px;
    height: 297px;
    border-radius: 16px;
    overflow: hidden;
    background: var(--card-black);
    box-shadow: 0 12px 30px rgba(0,0,0,.45);
  }
  .card--front { left: 140px; top: 140px; }
  .card--back { left: 540px; top: 500px; }

  /* Front */
  .front-name {
    position: absolute;
    left: 0; right: 0; top: 100px;
    text-align: center;
    font-family: "Lora", serif;
    font-weight: 400;
    font-size: 46px;
    line-height: 1;
    color: var(--ivory);
  }
  .front-tagline {
    position: absolute;
    left: 0; right: 0; bottom: 38px;
    text-align: center;
    font-family: "Lora", serif;
    font-weight: 700;
    font-size: 13px;
    color: var(--gold);
  }

  /* Back */
  .back-photo {
    position: absolute; inset: 0;
    background: linear-gradient(170deg, var(--photo-top) 0%, #1a1c20 45%, var(--photo-bottom) 100%);
  }
  .back-logo {
    position: absolute; right: 22px; top: 18px;
    font-family: "Lora", serif;
    font-weight: 400;
    font-size: 13px;
    color: var(--ivory);
  }
  .identity {
    position: absolute; left: 60px; top: 124px;
    width: 190px;
    text-align: right;
  }
  .identity__name {
    font-family: "Lora", serif;
    font-weight: 700;
    font-size: 22px;
    color: var(--gold);
  }
  .identity__role {
    font-family: "Lato", sans-serif;
    font-size: 12px;
    color: var(--text-light);
    margin-top: 2px;
  }
  .divider {
    position: absolute; left: 266px; top: 104px;
    width: 1px; height: 80px;
    background: var(--gold);
  }
  .contact {
    position: absolute; left: 282px; top: 100px;
    list-style: none;
    font-family: "Lato", sans-serif;
    font-size: 12.5px;
    line-height: 1.35;
    color: var(--text-light);
  }
  .contact__item { display: flex; align-items: flex-start; gap: 7px; margin-bottom: 4px; }
  .contact__icon { width: 11px; height: 11px; flex: none; margin-top: 3px; }
  .back-tagline {
    position: absolute; left: 0; right: 0; bottom: 30px;
    text-align: center;
    font-family: "Lora", serif;
    font-weight: 700;
    font-size: 13px;
    color: var(--gold);
  }
</style>
</head>
<body>
<main class="canvas">
  <section class="card card--front">
    <p class="front-name">Gilded Slatworks</p>
    <p class="front-tagline">Custom Plantation Shutters &amp; Motorized Architectural Shading Systems</p>
  </section>

  <section class="card card--back">
    <div class="back-photo" role="img" aria-label="Dimmed evening photo of a two-storey house with a covered porch and trees"></div>
    <p class="back-logo">Gilded Slatworks</p>
    <div class="identity">
      <p class="identity__name">Daniel Trevick</p>
      <p class="identity__role">Owner</p>
    </div>
    <div class="divider"></div>
    <ul class="contact">
      <li class="contact__item">
        <svg class="contact__icon" viewBox="0 0 12 12"><path d="M6 0.5a4 4 0 0 0-4 4c0 3 4 7 4 7s4-4 4-7a4 4 0 0 0-4-4z" fill="var(--gold)"/><circle cx="6" cy="4.5" r="1.5" fill="#111"/></svg>
        <span>240 Alder St, Suite 310 #2207<br>Millbrook, NC 28390</span>
      </li>
      <li class="contact__item">
        <svg class="contact__icon" viewBox="0 0 12 12"><path d="M2.5 1h2l1 3-1.3 1a6.5 6.5 0 0 0 2.8 2.8l1-1.3 3 1v2a1 1 0 0 1-1 1A9.5 9.5 0 0 1 1.5 2a1 1 0 0 1 1-1z" fill="var(--gold)"/></svg>
        <span>919-555-0148</span>
      </li>
      <li class="contact__item">
        <svg class="contact__icon" viewBox="0 0 12 12"><circle cx="6" cy="6" r="5" fill="none" stroke="var(--gold)" stroke-width="1.3"/><ellipse cx="6" cy="6" rx="2" ry="5" fill="none" stroke="var(--gold)" stroke-width="1"/><line x1="1" y1="6" x2="11" y2="6" stroke="var(--gold)" stroke-width="1"/></svg>
        <span>gildedslatworks.com</span>
      </li>
    </ul>
    <p class="back-tagline">Custom Interior &amp; Exterior Window Treatments</p>
  </section>
</main>
</body>
</html>
```